Garlic Farm for Farm Sales/Restaurant sales

Need a professional, but appealing to agriculture world. We are selling 27 kinds of Organic Garlic from a farm in Simla,CO. I have uploaded logo and business information-we are going to need a template, because I will need to use it for four separate people.
-We are trying to appeal to Farm to table restaurants
-As well as growers/farmers

Target Market(s)

Agriculture Sales/Restaurants-Organic

Industry/Entity Type

Agriculture

Contact Information for Business Card

Want it to look more unique then your average kelto stock card- I want it to look amazing

Font styles to use
Sans Serif

Colors
0455a3
ec1f27
fbed22
ffffff

Requirements
Must have
• Just be creative
Nice to have
• Colorful
Should not have
• plain

```html
<!DOCTYPE html>
<html lang="en">
<head>
<meta charset="utf-8">
<title>Ridgeline Garlic – Business Card</title>
<link rel="stylesheet" href="https://fonts.googleapis.com/css2?family=Open+Sans:wght@400;700;800&display=swap">
<style>
  :root {
    --navy: #1d3a70;
    --navy-deep: #1a3466;
    --red: #d3222a;
    --white: #ffffff;
    --backdrop: #2e2e30;
    --text-font: "Open Sans", Arial, sans-serif;
  }
  * { box-sizing: border-box; margin: 0; padding: 0; }
  html, body { width: 1200px; height: 880px; overflow: hidden; }
  body { background: var(--backdrop); font-family: var(--text-font); position: relative; }

  .card {
    position: absolute;
    width: 630px;
    height: 360px;
    box-shadow: 0 14px 30px rgba(0,0,0,.45);
  }

  /* Back of card */
  .card-back {
    left: 70px; top: 70px;
    background: var(--navy-deep);
    display: flex; align-items: center; justify-content: center;
  }
  .card-back .brand-name {
    color: var(--white);
    font-weight: 800;
    font-size: 46px;
    letter-spacing: 0.5px;
  }

  /* Front of card */
  .card-front {
    left: 500px; top: 450px;
    background: var(--white);
    color: var(--navy);
  }
  .name-marker {
    position: absolute; left: 0; top: 104px;
    width: 22px; height: 16px; background: var(--red);
  }
  .person-name {
    position: absolute; left: 44px; top: 94px;
    font-weight: 800; font-size: 24px;
  }
  .address {
    position: absolute; left: 110px; top: 168px;
    font-size: 17px; line-height: 22px;
  }
  .contact-list {
    position: absolute; left: 110px; top: 226px;
    list-style: none;
  }
  .contact-list li {
    display: flex; align-items: center; gap: 10px;
    font-size: 17px; line-height: 24px;
  }
  .contact-icon {
    width: 18px; height: 18px; background: var(--red);
    display: inline-flex; align-items: center; justify-content: center;
  }
  .social-row {
    position: absolute; left: 110px; top: 310px;
    display: flex; gap: 8px;
  }
  .social-slot { width: 26px; height: 26px; background: var(--red); }

  .logo {
    position: absolute; right: 40px; top: 40px;
    display: flex; align-items: center; gap: 14px;
  }
  .logo-dot {
    width: 62px; height: 62px; border-radius: 50%; background: var(--red);
  }
  .logo .brand-name {
    color: var(--navy);
    font-weight: 800;
    font-size: 30px;
  }
</style>
</head>
<body>

  <section class="card card-back" aria-label="Card back">
    <span class="brand-name">Ridgeline Garlic</span>
  </section>

  <section class="card card-front" aria-label="Card front">
    <div class="logo">
      <span class="logo-dot"></span>
      <span class="brand-name">Ridgeline Garlic</span>
    </div>

    <span class="name-marker"></span>
    <h1 class="person-name">Dana Merritt</h1>

    <p class="address">P.O. Box 48 Elmhaven,<br>CO 80912</p>

    <ul class="contact-list">
      <li>
        <span class="contact-icon">
          <svg width="12" height="12" viewBox="0 0 24 24" aria-hidden="true"><path fill="#fff" d="M6.6 10.8a15 15 0 0 0 6.6 6.6l2.2-2.2c.3-.3.7-.4 1-.2 1.1.4 2.3.6 3.6.6.6 0 1 .4 1 1V20c0 .6-.4 1-1 1A17 17 0 0 1 3 4c0-.6.4-1 1-1h3.5c.6 0 1 .4 1 1 0 1.3.2 2.5.6 3.6.1.3 0 .7-.2 1z"/></svg>
        </span>
        555-014-2290
      </li>
      <li>
        <span class="contact-icon">
          <svg width="12" height="12" viewBox="0 0 24 24" aria-hidden="true"><rect x="2" y="5" width="20" height="14" fill="none" stroke="#fff" stroke-width="2"/><path d="M2 5l10 8 10-8" fill="none" stroke="#fff" stroke-width="2"/></svg>
        </span>
        Dana@RidgelineGarlic.com
      </li>
      <li>
        <span class="contact-icon">
          <svg width="12" height="12" viewBox="0 0 24 24" aria-hidden="true"><circle cx="12" cy="12" r="9" fill="none" stroke="#fff" stroke-width="2"/><path d="M3 12h18M12 3c3 3 3 15 0 18M12 3c-3 3-3 15 0 18" fill="none" stroke="#fff" stroke-width="1.6"/></svg>
        </span>
        RidgelineGarlic.com
      </li>
    </ul>

    <div class="social-row" aria-label="Social profiles">
      <span class="social-slot"></span>
      <span class="social-slot"></span>
      <span class="social-slot"></span>
      <span class="social-slot"></span>
    </div>
  </section>

</body>
</html>
```